CREATE A BUSINESS CARD FOR A BOAT CLEANING SERVICE

WE ARE STARTING A NEW BOAT CLEANING BUSINESS. WE DIVE UNDERWATER TO CLEAN BOAT HULLS, JETTIES, UNDERWATER STRUCTURES ETC. WE ARE LOOKING FOR AN UPPERMARKET MODERN LOGO AND BUSINESS CARD AS ALOT OF OUR TARGET MARKET WILL BE HIGH END. YOU HAVE TO DESIGN A BUSINESS CARD AND LOGO SEPERATELY .
THE BUSINESS CARD DIMESNION MUST BE STANDARD SIZE.
The standard dimensions of a printed business card are 3.5 x 2 inches

Target Market(s)

UNDERWATER SERVICED

Industry/Entity Type

Business

Contact Information for Business Card

HOLLAND UNDERWATER SERVICES

Font styles to use
Serif

Colors

Designer to choose colors to be used in the design.

Requirements
Must have
• HOLLAND
Nice to have
• dark
Should not have
• more than 3 colors

```html
<!DOCTYPE html>
<html lang="en">
<head>
<meta charset="utf-8">
<title>Holland Underwater Services – Business Card</title>
<link href="https://fonts.googleapis.com/css2?family=Lato:wght@400;700&display=swap" rel="stylesheet">
<style>
  :root {
    --backdrop: #555555;
    --card-white: #ffffff;
    --navy: #15508b;
    --slate: #7a7a7a;
    --ink: #1a1a1a;
    --rule: #8a8fa8;
  }
  html, body {
    margin: 0;
    padding: 0;
    width: 1200px;
    height: 900px;
    overflow: hidden;
    background: var(--backdrop);
    font-family: "Lato", Arial, sans-serif;
  }
  .canvas {
    position: relative;
    width: 1200px;
    height: 900px;
  }
  .card {
    position: absolute;
    top: 170px;
    width: 347px;
    height: 561px;
    overflow: hidden;
  }
  .card--front { left: 259px; background: var(--card-white); text-align: center; color: var(--ink); }
  .card--back { left: 631px; background: var(--slate); }

  .brand {
    position: absolute;
    top: 178px;
    left: 0;
    width: 100%;
    color: var(--navy);
    font-weight: 400;
  }
  .brand__name {
    display: block;
    font-size: 48px;
    line-height: 1;
    letter-spacing: 3px;
  }
  .brand__tagline {
    display: block;
    margin-top: 6px;
    font-size: 15.5px;
    letter-spacing: 2.4px;
  }

  .contact {
    position: absolute;
    top: 339px;
    left: 0;
    width: 100%;
    font-size: 15px;
    line-height: 21px;
  }
  .contact__name {
    margin: 0;
    color: var(--navy);
    font-size: 21px;
    font-weight: 700;
    line-height: 28px;
  }
  .contact__role { margin: 0; }
  .contact__rule {
    width: 130px;
    height: 1px;
    margin: 10px auto;
    border: 0;
    background: var(--rule);
  }
  .contact__list { margin: 0; padding: 0; list-style: none; }
  .contact__label { color: var(--navy); font-weight: 700; }
  .contact__web { color: var(--navy); font-weight: 700; }
  .contact__address { margin: 0; line-height: 18px; }

  .back__sea {
    position: absolute;
    inset: 0;
  }
  .back__brand {
    position: absolute;
    top: 205px;
    left: 0;
    width: 100%;
    text-align: center;
    color: var(--card-white);
    font-size: 42px;
    font-weight: 400;
    letter-spacing: 3px;
  }
  .back__services {
    position: absolute;
    top: 450px;
    left: 0;
    width: 100%;
    margin: 0;
    text-align: center;
    color: var(--card-white);
    font-size: 16.5px;
    line-height: 27px;
    text-transform: uppercase;
  }
</style>
</head>
<body>
<main class="canvas">
  <section class="card card--front" aria-label="Business card front">
    <div class="brand">
      <span class="brand__name">HOLLAND</span>
      <span class="brand__tagline">UNDERWATER SERVICES</span>
    </div>
    <div class="contact">
      <h1 class="contact__name">MARK DEVLIN</h1>
      <p class="contact__role">Managing Director</p>
      <hr class="contact__rule">
      <ul class="contact__list">
        <li><span class="contact__label">P:</span> 555-218-4470</li>
        <li><span class="contact__label">E:</span> hello@hollanddive.com</li>
        <li class="contact__web">www.hollanddive.com</li>
      </ul>
      <hr class="contact__rule">
      <p class="contact__address">48 Harbour Quay Road<br>Marina Bay, 204817</p>
    </div>
  </section>

  <section class="card card--back" aria-label="Business card back">
    <svg class="back__sea" width="347" height="561" viewBox="0 0 347 561" aria-hidden="true">
      <path d="M0 287 C 120 262, 300 280, 347 230 L 347 561 L 0 561 Z" fill="var(--navy)"/>
    </svg>
    <div class="back__brand">HOLLAND</div>
    <p class="back__services">We dive underwater to clean<br>boat,hulls,jetties, underwater<br>structures etc</p>
  </section>
</main>
</body>
</html>
```